Business Card Design Project

I have established a company called "Corvella" which is a business specialising in psychotherapy/counselling , predominantly for anxiety & depression.

My name is Nel....hence, the Corvella link. However, Corvella was also chosen for its reference to green shoots of growth/recovery.

Corvella is to be "upmarket" and highly professional. I'm keen for the style and colours to reflect this.....taupe/grey with navy/black script, for example.....NO primary colours.

My name needs to be on the card and my mobile number. Not sure, but suspect it should also have my qualifications ( BA (Psych) & BSc (Hons) Psychology). Mobile number 0412 903 618.

```html
<!DOCTYPE html>
<html lang="en">
<head>
<meta charset="utf-8">
<title>Corvella – Business Card</title>
<link href="https://fonts.googleapis.com/css2?family=Lato:wght@300;400;700&family=Roboto+Condensed:wght@700&display=swap" rel="stylesheet">
<style>
  :root {
    --page: #e6e6e4;
    --card: #ffffff;
    --leaf: #3db54a;
    --leaf-light: #a9dba9;
    --name: #4a4ea6;
    --brand: #8cc63f;
    --ink: #111111;
    --label: #1a1a1a;
  }
  * { margin: 0; padding: 0; box-sizing: border-box; }
  html, body { width: 1026px; height: 1200px; overflow: hidden; }
  body { background: var(--page); font-family: "Lato", sans-serif; position: relative; }

  .card {
    position: absolute;
    left: 193px;
    width: 640px;
    height: 370px;
    background: var(--card);
    box-shadow: 0 6px 18px rgba(0,0,0,0.18);
    overflow: hidden;
  }
  .card--front { top: 110px; }
  .card--back { top: 640px; }

  .card-label {
    position: absolute;
    left: 193px;
    font-family: "Roboto Condensed", sans-serif;
    font-weight: 700;
    font-size: 22px;
    color: var(--label);
  }
  .card-label--front { top: 490px; }
  .card-label--back { top: 1020px; }

  /* front */
  .leaf-art {
    position: absolute;
    left: 0; top: 0;
    width: 150px; height: 100%;
    background: linear-gradient(90deg, var(--leaf) 0%, var(--leaf) 60%, var(--leaf-light) 100%);
  }
  .identity {
    position: absolute;
    right: 32px; top: 62px;
    text-align: right;
  }
  .identity__name {
    font-weight: 300;
    font-size: 64px;
    line-height: 0.95;
    color: var(--name);
    letter-spacing: 1px;
  }
  .identity__brand {
    font-weight: 400;
    font-size: 36px;
    line-height: 1;
    color: var(--brand);
    margin-top: -2px;
  }
  .identity__details {
    margin-top: 8px;
    font-size: 17px;
    line-height: 1.55;
    color: var(--ink);
    font-weight: 400;
  }
  .growth-band {
    position: absolute;
    left: 138px; right: 0;
    top: 286px; height: 24px;
    background: var(--leaf);
    border-radius: 3px 0 0 3px;
  }
  .front-tagline {
    position: absolute;
    left: 208px; top: 318px;
    font-size: 23px;
    color: var(--ink);
  }

  /* back */
  .back-art {
    position: absolute;
    left: 220px; top: 34px;
    width: 240px; height: 112px;
    background: linear-gradient(90deg, var(--leaf) 0%, var(--leaf) 60%, var(--leaf-light) 100%);
  }
  .back-statement {
    position: absolute;
    left: 0; right: 0; top: 168px;
    text-align: center;
    font-family: "Roboto Condensed", sans-serif;
    font-weight: 700;
    font-size: 36px;
    line-height: 1.2;
    color: var(--ink);
    letter-spacing: 0.5px;
  }
</style>
</head>
<body>
  <section class="card card--front" aria-label="Card front">
    <div class="leaf-art" role="img" aria-label="Green leaf shoot illustration"></div>
    <div class="identity">
      <div class="identity__name">NEL</div>
      <div class="identity__brand">Corvella</div>
      <div class="identity__details">
        BA (Psych)<br>
        BSc (Hons) Psychology<br>
        Mobile: 0412 903 618
      </div>
    </div>
    <div class="growth-band"></div>
    <p class="front-tagline">specialising in psychotherapy</p>
  </section>
  <div class="card-label card-label--front">Front</div>

  <section class="card card--back" aria-label="Card back">
    <div class="back-art" role="img" aria-label="Green leaf shoot illustration"></div>
    <p class="back-statement">
      specialising in psychotherapy<br>
      predominantly for anxiety<br>
      &amp; depression.
    </p>
  </section>
  <div class="card-label card-label--back">Back</div>
</body>
</html>
```